Commercial Waterproofing Modern Business Cards

We are a Commercial Waterproofing company. We do a variety of jobs on the exterior of buildings. We repel from the top or scaffold to reach the areas. Cut out and recaulk expansion joints and apply sealants, brick/concrete repairs, seal window frame perimeters, and much more. Our website is www.tallwallmend.com.
We are looking for a new business card design that would look more modern and cutting edge. We like the transparent paper and had thought about using our logo, but maybe pulling it apart to where the building part is kind of in the background. I have attached 2 different logos that we use regularly. We want the design to be a little funky, but professional at the same time. We really don't want the logo to be incorporated by itself, but you can use the logo and take out the buildings and just use the name or vice versa. Please don't just put the logo on the card and the words around that.

Target Market(s)

Property Managers/Building Maintenance

Industry/Entity Type

Business

Contact Information for Business Card

Dorian Vellstrom President
Office (555)418-2097
Mobile (555)604-7351

Font styles to use
Serif

Requirements
Must have
• Nice overall design, somehow pulling from the logo for the design
Nice to have
• Look artsy and modern with a nice quality paper
Should not have
• Too many words or distracting designs. The logo 'as is'

```html
<!DOCTYPE html>
<html lang="en">
<head>
<meta charset="utf-8">
<title>TallWall Mend — Business Card</title>
<link rel="stylesheet" href="https://fonts.googleapis.com/css2?family=Tinos:wght@400;700&display=swap">
<style>
  :root {
    --backdrop: #2a2a2c;
    --paper-light: #f4f4f3;
    --paper-mid: #e3e3e1;
    --paper-shade: #cfd0cf;
    --brand-blue: #1f4f97;
    --text-grey: #555658;
    --facet-pale: #d6e8f6;
    --facet-mid: #9cc9ea;
    --facet-deep: #3f8fd0;
  }
  * { margin: 0; padding: 0; box-sizing: border-box; }
  html, body {
    width: 1200px;
    height: 834px;
    overflow: hidden;
  }
  body {
    background: var(--backdrop);
    display: flex;
    align-items: center;
    justify-content: center;
    font-family: "Tinos", "Times New Roman", serif;
  }
  .business-card {
    position: relative;
    width: 840px;
    height: 520px;
    background: linear-gradient(100deg, var(--paper-light) 0%, var(--paper-mid) 45%, var(--paper-light) 70%, var(--paper-shade) 100%);
    overflow: hidden;
  }
  .facet-field {
    position: absolute;
    top: 0;
    right: 0;
    width: 430px;
    height: 100%;
    background:
      linear-gradient(90deg, rgba(244,244,243,1) 0%, rgba(244,244,243,0) 45%),
      linear-gradient(160deg, var(--facet-pale) 0%, var(--facet-mid) 45%, var(--facet-deep) 100%);
  }
  .brand {
    position: absolute;
    left: 70px;
    top: 62px;
    display: flex;
    align-items: center;
    gap: 12px;
  }
  .brand-mark {
    width: 34px;
    height: 34px;
    background: var(--brand-blue);
  }
  .brand-name {
    font-size: 30px;
    font-weight: 700;
    color: var(--brand-blue);
  }
  .contact {
    position: absolute;
    left: 70px;
    top: 268px;
  }
  .contact-name {
    font-size: 31px;
    font-weight: 700;
    color: var(--brand-blue);
    line-height: 1.1;
  }
  .contact-role {
    font-size: 24px;
    font-weight: 700;
    color: var(--text-grey);
    line-height: 1.2;
  }
  .contact-phones {
    margin-top: 26px;
    font-size: 30px;
    color: var(--text-grey);
    line-height: 1.3;
    list-style: none;
  }
</style>
</head>
<body>
  <article class="business-card">
    <div class="facet-field" role="img" aria-label="Faceted pattern of translucent blue triangles"></div>
    <header class="brand">
      <span class="brand-mark"></span>
      <span class="brand-name">TallWall Mend</span>
    </header>
    <section class="contact">
      <h1 class="contact-name">Dorian VELLSTROM</h1>
      <p class="contact-role">President Office</p>
      <ul class="contact-phones">
        <li>(555)418-2097</li>
        <li>(555)604-7351</li>
      </ul>
    </section>
  </article>
</body>
</html>
```